Structural Engineering Business Card

Brookvane Drafting does residential house plans for clients in Central Florida. Would like simple but elegant business card that is appropriate for a house plan engineering company. Prefer black business card with black/white them but open to other shades of blue. I uploaded a sample card that I came across that looked good but please come up with your own creative designs.

Contact Information for Business Card

Name, Title, Phone, Email, Address, website

```html
<!DOCTYPE html>
<html lang="en">
<head>
<meta charset="utf-8">
<title>Brookvane Drafting – Business Card</title>
<link rel="stylesheet" href="https://fonts.googleapis.com/css2?family=Arimo:wght@400;700&display=swap">
<style>
  :root {
    --backdrop: #e4e4e4;
    --card: #333333;
    --ink: #ffffff;
    --ink-soft: #d9d9d9;
    --rule: #bdbdbd;
  }
  * { box-sizing: border-box; margin: 0; padding: 0; }
  html, body {
    width: 1200px; height: 802px; overflow: hidden;
    background: var(--backdrop);
    font-family: "Arimo", Arial, sans-serif;
    color: var(--ink);
  }
  .stage {
    width: 1200px; height: 802px;
    display: flex; align-items: center; justify-content: center; gap: 48px;
  }
  .card {
    position: relative;
    width: 530px; height: 303px;
    background: var(--card);
    border-radius: 3px;
    box-shadow: 0 6px 18px rgba(0,0,0,.18);
    overflow: hidden;
  }
  .brand {
    font-weight: 700; color: var(--ink);
    letter-spacing: .5px; text-transform: uppercase;
    display: flex; align-items: center; gap: 10px; white-space: nowrap;
  }
  .brand-mark { width: 14px; height: 14px; background: var(--ink); }

  /* front */
  .card-front .brand { position: absolute; top: 46px; left: 0; right: 0; justify-content: center; font-size: 24px; }
  .card-front .top-rule { position: absolute; top: 104px; left: 190px; right: 0; height: 1px; background: var(--rule); }
  .card-front .address { position: absolute; top: 122px; right: 28px; text-align: right; font-size: 14px; line-height: 1.3; color: var(--ink-soft); }
  .person { position: absolute; left: 26px; bottom: 112px; }
  .person-name { font-size: 18px; font-weight: 700; letter-spacing: .5px; text-transform: uppercase; }
  .person-title { font-size: 13px; color: var(--ink-soft); margin-top: 2px; }
  .card-front .name-rule { position: absolute; left: 26px; bottom: 100px; width: 270px; height: 1px; background: var(--rule); }
  .contacts { position: absolute; left: 26px; bottom: 22px; list-style: none; font-size: 14px; color: var(--ink-soft); }
  .contacts li { display: flex; align-items: center; gap: 9px; height: 24px; }
  .contacts svg { width: 12px; height: 12px; fill: var(--ink); flex: none; }

  /* back */
  .card-back .brand { position: absolute; left: 36px; bottom: 44px; font-size: 34px; }
</style>
</head>
<body>
<main class="stage">
  <section class="card card-front" aria-label="Card front">
    <div class="brand"><span class="brand-mark"></span>Brookvane Drafting</div>
    <div class="top-rule"></div>
    <p class="address">Your Address, City<br>State, Zip 0000</p>
    <div class="person">
      <p class="person-name">Daniel Reyes</p>
      <p class="person-title">Manager</p>
    </div>
    <div class="name-rule"></div>
    <ul class="contacts">
      <li><svg viewBox="0 0 24 24"><path d="M6.6 10.8a15 15 0 0 0 6.6 6.6l2.2-2.2c.3-.3.7-.4 1-.2 1.1.4 2.3.6 3.6.6.6 0 1 .4 1 1V20c0 .6-.4 1-1 1A17 17 0 0 1 3 4c0-.6.4-1 1-1h3.5c.6 0 1 .4 1 1 0 1.3.2 2.5.6 3.6.1.3 0 .7-.2 1z"/></svg>123-456-2100</li>
      <li><svg viewBox="0 0 24 24"><path d="M2 5h20v14H2zm2 2v.5l8 5 8-5V7zm0 2.8V17h16V9.8l-8 5z"/></svg>daniel@brookvane.com</li>
      <li><svg viewBox="0 0 24 24"><path d="M12 2a10 10 0 1 0 0 20 10 10 0 0 0 0-20zm0 2a8 8 0 0 1 0 16 8 8 0 0 1 0-16z"/><circle cx="12" cy="12" r="4"/></svg>www.brookvane.com</li>
    </ul>
  </section>

  <section class="card card-back" aria-label="Card back">
    <div class="brand"><span class="brand-mark"></span>Brookvane Drafting</div>
  </section>
</main>
</body>
</html>
```